Need Flyer for Our Real estate Agency

Need to run General Campaign for our agency with Start of New Year as our theme ..Must have an agent's picture on the DL..
Address:
27 / 486Brindle rd, Marsden VIC 3047
Ph:03 9412 7306
email:info@kovalinrealestate.com.au
www.kovalinrealestate.com.au
Something like as attached picture..
Target Market(s)
Home Buyers
Industry/Entity Type
Real Estate Agent
Requirements
Must have
- Our Logo Colours

```html
<!DOCTYPE html>
<html lang="en">
<head>
<meta charset="UTF-8">
<title>Kovalin Real Estate – Banner</title>
<link href="https://fonts.googleapis.com/css2?family=Jost:wght@400;500;600;700&family=Montserrat:wght@700;800&display=swap" rel="stylesheet">
<style>
  :root {
    --navy: #0f1182;
    --navy-deep: #0b0d6c;
    --white: #ffffff;
    --backdrop: #e4e7e7;
    --chevron: rgba(80, 90, 200, 0.45);
    --photo-light: #8c8f86;
    --photo-dark: #2a2c30;
  }
  * { margin: 0; padding: 0; box-sizing: border-box; }
  html, body { width: 1200px; height: 900px; overflow: hidden; }
  body {
    background: var(--backdrop);
    font-family: "Jost", "Century Gothic", sans-serif;
    position: relative;
  }
  .banner {
    position: absolute;
    left: 50px; top: 168px;
    width: 1103px; height: 552px;
    background: var(--navy);
    overflow: hidden;
    color: var(--white);
  }
  .banner__photo {
    position: absolute; inset: 0;
    width: 1103px; height: 552px;
  }
  .brand {
    position: absolute;
    left: 175px; top: 160px;
    width: 360px;
    text-align: center;
    font-family: "Jost", sans-serif;
    font-weight: 500;
    color: var(--white);
    letter-spacing: 0.12em;
  }
  .brand__name { font-size: 62px; line-height: 1; display: block; }
  .brand__tagline { font-size: 17px; display: block; margin-top: 14px; letter-spacing: 0.18em; }
  .contact__title {
    position: absolute;
    left: 32px; top: 284px;
    font-family: "Montserrat", sans-serif;
    font-weight: 800;
    font-size: 23px;
  }
  .contact__box {
    position: absolute;
    left: 32px; top: 325px;
    width: 422px; height: 122px;
    border: 1.5px solid var(--white);
    border-radius: 14px;
    padding: 10px 0 0 12px;
    list-style: none;
  }
  .contact__item {
    display: flex; align-items: center;
    height: 38px;
    font-size: 18px;
    font-weight: 400;
  }
  .contact__icon { width: 26px; height: 26px; margin-right: 14px; flex: none; }
  .chevrons { position: absolute; left: 493px; top: 337px; width: 134px; height: 102px; }
  .call-now {
    position: absolute;
    left: 0; top: 465px;
    width: 234px; height: 71px;
    background: var(--white);
    border-radius: 0 12px 12px 0;
    color: var(--navy);
    font-family: "Montserrat", sans-serif;
    font-weight: 700;
    font-size: 29px;
    display: flex; align-items: center; justify-content: center;
  }
  .phone {
    position: absolute;
    left: 281px; top: 473px;
    display: flex; align-items: center;
  }
  .phone__icon { width: 55px; height: 55px; margin-right: 31px; }
  .phone__number { font-size: 40px; font-weight: 500; letter-spacing: 0.03em; }
</style>
</head>
<body>
  <section class="banner">
    <svg class="banner__photo" viewBox="0 0 1103 552" role="img" aria-label="Photo of a smiling real estate agent in a dark suit with arms crossed">
      <defs>
        <linearGradient id="photoTone" x1="0" y1="0" x2="0.6" y2="1">
          <stop offset="0" stop-color="var(--photo-light)"/>
          <stop offset="0.55" stop-color="#5e6160"/>
          <stop offset="1" stop-color="var(--photo-dark)"/>
        </linearGradient>
      </defs>
      <circle cx="1133" cy="276" r="431" fill="url(#photoTone)" stroke="var(--white)" stroke-width="5"/>
    </svg>

    <div class="brand">
      <span class="brand__name">KOVALIN</span>
      <span class="brand__tagline">REAL ESTATE</span>
    </div>

    <h2 class="contact__title">CONTACT US:</h2>
    <ul class="contact__box">
      <li class="contact__item">
        <svg class="contact__icon" viewBox="0 0 26 26"><circle cx="13" cy="13" r="13" fill="#fff"/><path d="M13 5.5a5 5 0 0 0-5 5c0 4 5 9.5 5 9.5s5-5.5 5-9.5a5 5 0 0 0-5-5z" fill="var(--navy)"/><circle cx="13" cy="10.5" r="2" fill="#fff"/></svg>
        27 / 486Brindle rd, Marsden VIC 3047
      </li>
      <li class="contact__item">
        <svg class="contact__icon" viewBox="0 0 26 26"><circle cx="13" cy="13" r="13" fill="#fff"/><rect x="6.5" y="8.5" width="13" height="9" fill="none" stroke="var(--navy)" stroke-width="1.6"/><path d="M6.5 8.5l6.5 5 6.5-5" fill="none" stroke="var(--navy)" stroke-width="1.6"/></svg>
        email:info@kovalinrealestate.com.au
      </li>
      <li class="contact__item">
        <svg class="contact__icon" viewBox="0 0 26 26"><circle cx="13" cy="13" r="13" fill="#fff"/><g fill="none" stroke="var(--navy)" stroke-width="1.4"><circle cx="13" cy="13" r="7"/><ellipse cx="13" cy="13" rx="3" ry="7"/><path d="M6 13h14M7 9.5h12M7 16.5h12"/></g></svg>
        www.kovalinrealestate.com.au
      </li>
    </ul>

    <svg class="chevrons" viewBox="0 0 134 102" aria-hidden="true">
      <path d="M0 0h28l50 51-50 51H0l50-51z" fill="none" stroke="var(--chevron)" stroke-width="6"/>
      <path d="M52 0h28l50 51-50 51H52l50-51z" fill="var(--chevron)"/>
    </svg>

    <div class="call-now">CALL NOW</div>
    <div class="phone">
      <svg class="phone__icon" viewBox="0 0 55 55"><circle cx="27.5" cy="27.5" r="27.5" fill="#fff"/><path d="M19 14c1-1 2.5-1 3.3 0l3 4c.7 1 .6 2.3-.3 3.1l-1.8 1.6c1.5 3.3 4 5.9 7.2 7.4l1.6-1.8c.8-.9 2.1-1 3.1-.3l4 3c1 .8 1 2.3 0 3.3l-2 2c-1.6 1.6-4 2-6 1-7-3.2-12.3-8.5-15.4-15.5-.9-2-.5-4.4 1.1-6z" fill="var(--navy)"/></svg>
      <span class="phone__number">03 9412 7306</span>
    </div>
  </section>
</body>
</html>
```